Rack Card for Charter Sail Boat business in SF Bay

We are in need of a rack card design to highlight the business to tourists and locals. 2 sided card 3.86" x 8.39" (full bleed)

We are looking for visually appleaing designs on the front and back but a little more detail on the back.

Use the info provided (text and info) on the website to include the 3 key services (Quick, 1/2 day, fullday) and aspects of the boat, location and other key info for customers (not prices). DO NOT INCLUDE ALL THIS TEXT please pick the elements you would like to fit your design and inform the customer as you would like about the business.

I can also provide photos directly from the video if you think those would fit your design. If video doesn't work on this upload you can view it at the website or facebook page (www.fb.com/tidewrenmarinellc)

Target Market(s)

Tourists and locals to san francisco east bay. 25 - 55 years old. Men and women.

Industry/Entity Type

Entertainment

Colors
0455a3
ec1f27
f3f1f8

Requirements
Must have
• Highlight services, key contact information (email, phone, website site), Visual impact
• 2-sided card - 3.86" x 8.39" (98 x 213 mm)
Nice to have
• facebook link, electric engine(green),

```html
<!DOCTYPE html>
<html lang="en">
<head>
<meta charset="utf-8">
<title>Tidewren Marine – Rack Card</title>
<link rel="stylesheet" href="https://fonts.googleapis.com/css2?family=Arimo:wght@400;700&family=Libre+Baskerville:ital,wght@0,700;1,400&family=Oswald:wght@300;400;500;600&display=swap">
<style>
  :root{
    --blue:#0455a3;
    --navy:#1a4b96;
    --red:#ec1f27;
    --red-deep:#c8141c;
    --paper:#f3f1f8;
    --white:#ffffff;
    --yellow:#ffe600;
    --ink:#1a1a1a;
    --stage:#e6e3ec;
  }
  *{box-sizing:border-box;margin:0;padding:0}
  html,body{width:1200px;height:1200px;overflow:hidden;background:var(--stage)}
  .stage{position:relative;width:1200px;height:1200px}
  .card{position:absolute;width:556px;height:1208px;overflow:hidden;transform:scale(.8);transform-origin:0 0;background:var(--white);box-shadow:0 4px 14px rgba(0,0,0,.25)}
  .card--front{left:137px;top:124px}
  .card--back{left:645px;top:124px;background:var(--blue)}
  .card-bg{position:absolute;inset:0;width:556px;height:1208px}
  .photo-circle{position:absolute;border-radius:50%;border:10px solid var(--white)}
  .abs{position:absolute}

  .brand{position:absolute;left:300px;top:70px;display:flex;align-items:center;gap:10px;font-family:"Libre Baskerville",serif;font-weight:700;font-size:34px;color:var(--navy);background:rgba(255,255,255,.92);padding:10px 16px;border-radius:6px}
  .brand-dot{width:16px;height:16px;border-radius:50%;background:var(--red)}
  .tagline{position:absolute;left:20px;top:362px;width:260px;font-family:"Libre Baskerville",serif;font-style:italic;font-size:26px;line-height:34px;color:var(--white)}

  .feature h2{font-family:"Libre Baskerville",serif;font-weight:700;font-size:22px;line-height:26px;margin-bottom:4px}
  .feature p{font-family:Arimo,sans-serif;font-size:15px;line-height:17.6px;color:var(--ink)}
  .feature--red h2{color:var(--red-deep)}
  .feature--blue h2{color:var(--blue)}
  .feature--modern{left:261px;top:625px;width:268px}
  .feature--entertaining{left:258px;top:803px;width:274px}
  .feature--safe{left:19px;top:838px;width:214px}

  .contact{font-family:Oswald,sans-serif;font-weight:500;font-size:17px;color:var(--white);display:flex;align-items:center;gap:8px;white-space:nowrap}
  .contact svg{width:22px;height:22px;flex:none}
  .contact--phone-front{position:absolute;left:22px;top:1130px}
  .contact--mail-front{position:absolute;left:22px;top:1160px}

  .trip-title{position:absolute;left:24px;top:18px;font-family:Oswald,sans-serif;font-weight:600;font-size:22px;color:var(--white);letter-spacing:-.3px}
  .trip-copy{position:absolute;left:22px;top:56px;width:512px;font-family:Arimo,sans-serif;font-size:16px;line-height:17.6px;color:var(--white)}

  .service{position:absolute;border-radius:50%;border:9px solid var(--white);display:flex;flex-direction:column;align-items:center;justify-content:center;text-align:center;padding:0 24px}
  .service h3{font-family:Oswald,sans-serif;font-weight:600;font-size:29px;line-height:30px;color:var(--yellow);margin-bottom:8px;letter-spacing:-.5px}
  .service p{font-family:Oswald,sans-serif;font-weight:300;font-size:16px;line-height:21.5px;color:var(--white)}
  .service--red{background:var(--red-deep)}
  .service--blue{background:var(--blue)}
  .service--quick{left:288px;top:255px;width:250px;height:250px}
  .service--half{left:19px;top:480px;width:244px;height:244px}
  .service--full{left:296px;top:732px;width:246px;height:246px}
  .service--full h3{margin-bottom:10px}

  .badge{position:absolute;left:14px;top:1005px;width:94px;height:94px;border-radius:50%;background:var(--navy);border:4px solid var(--yellow)}
  .contact--phone-back{position:absolute;left:46px;top:1126px}
  .contact--mail-back{position:absolute;left:270px;top:1126px}
  .contact--web-back{position:absolute;left:78px;top:1166px;font-size:16px}
  .contact--social-back{position:absolute;left:306px;top:1166px;font-size:16px}
  .social-dot{width:20px;height:20px;border-radius:50%;border:2px solid var(--white)}
</style>
</head>
<body>
<main class="stage">

  <!-- FRONT -->
  <section class="card card--front" aria-label="Rack card front">
    <svg class="card-bg" viewBox="0 0 556 1208" aria-hidden="true">
      <defs>
        <linearGradient id="sunsetSea" x1="0" y1="0" x2="0" y2="1">
          <stop offset="0" stop-color="#3d5f8c"/>
          <stop offset=".42" stop-color="#e7c48a"/>
          <stop offset=".5" stop-color="#f4d9a0"/>
          <stop offset=".58" stop-color="#4f6a8a"/>
          <stop offset="1" stop-color="#243c5c"/>
        </linearGradient>
      </defs>
      <g role="img" aria-label="Photo: view from the cockpit of a sailboat toward a sunset over the bay">
        <rect x="0" y="0" width="556" height="360" fill="url(#sunsetSea)"/>
      </g>
      <path d="M0 285 C140 250 330 265 490 345 L556 350 L556 600 L0 600 Z" fill="var(--red-deep)"/>
      <path d="M0 318 C150 292 330 305 470 372 L556 380 L556 592 C420 560 260 570 0 560 Z" fill="var(--navy)"/>
      <path d="M175 592 C300 565 430 555 556 565 L556 585 C430 575 300 582 175 592 Z" fill="var(--red-deep)"/>
      <path d="M300 1140 C410 1135 500 1115 556 1080 L556 1200 C470 1180 380 1160 300 1140 Z" fill="var(--red-deep)"/>
      <path d="M0 1098 C160 1080 360 1115 556 1205 L556 1208 L0 1208 Z" fill="var(--navy)"/>
    </svg>

    <div class="brand"><span class="brand-dot"></span>Tidewren</div>
    <p class="tagline">Enjoy an amazing experience aboard Tidewren and view San Francisco and the rest of the bay</p>

    <div class="photo-circle" role="img" aria-label="Photo: sails and deck under a clear blue sky over the bay"
         style="left:270px;top:300px;width:300px;height:310px;background:linear-gradient(160deg,#1c4d9c 0%,#5f8fcf 45%,#8aa9c6 62%,#2b4f7a 100%)"></div>
    <div class="photo-circle" role="img" aria-label="Photo: dark-hulled sailboat moored at a marina"
         style="left:-34px;top:555px;width:260px;height:260px;background:linear-gradient(180deg,#8fb1d8 0%,#c7d4e2 40%,#1d2433 62%,#3d7a8c 100%)"></div>
    <div class="photo-circle" role="img" aria-label="Photo: guests in life jackets enjoying the sail"
         style="left:410px;top:1058px;width:160px;height:160px;background:linear-gradient(160deg,#6e7d8a 0%,#c7ccd1 40%,#c23a3a 65%,#e0c020 100%)"></div>

    <article class="abs feature feature--red feature--modern">
      <h2>Modern</h2>
      <p>Tidewren is completely electric which means no diesel smells, noise or vibration to suffer. New electrics, plumbing, toilets, and deck areas compliment the elegant lines and features of this Marlowe 46 foot cutter rigged sailboat.</p>
    </article>
    <article class="abs feature feature--blue feature--entertaining">
      <h2>Entertaining</h2>
      <p>Surrounded by the beauty and wonder of the San Francisco Bay you will enjoy the choice of sounds from your source, satellite radio, CD or old school FM! Experience the thrill of sailing Tidewren while we explore Alcatraz and Angel Islands', The Golden Gate and Bay Bridges, the City front or the many other hidden gems. While taking it all in, you and your guests can enjoy refreshments and snacks we provide or even choose to have lunch or dinner at anchor or on a private beach!</p>
    </article>
    <article class="abs feature feature--red feature--safe">
      <h2>Safe</h2>
      <p>We carry aboard everything to make your time aboard safe. Life preservers are of course provided and available for all including kids sizes. We carry the USCG bulky ones as well as modern self inflating slim comfortable life jackets. Also loaded for every trip is a complete first aid kit, AED, EPIRB, and many other safety items</p>
    </article>

    <div class="contact contact--phone-front">
      <svg viewBox="0 0 24 24" aria-hidden="true"><circle cx="12" cy="12" r="10.5" fill="none" stroke="#fff" stroke-width="1.6"/><path d="M8.6 6.8l1.7-.4 1 2.5-1.2 1a7 7 0 003.9 3.9l1-1.2 2.5 1-.4 1.7c-4.7.3-8.8-3.8-8.5-8.5z" fill="#fff"/></svg>
      +1 (510) 555 SAIL (7245)
    </div>
    <div class="contact contact--mail-front">
      <svg viewBox="0 0 24 24" aria-hidden="true"><rect x="2" y="5" width="20" height="14" fill="none" stroke="#fff" stroke-width="1.6"/><path d="M2 5l10 8 10-8M2 19l7-6M22 19l-7-6" fill="none" stroke="#fff" stroke-width="1.6"/></svg>
      Bookings@TidewrenMarine.com
    </div>
  </section>

  <!-- BACK -->
  <section class="card card--back" aria-label="Rack card back">
    <svg class="card-bg" viewBox="0 0 556 1208" aria-hidden="true">
      <defs>
        <linearGradient id="bayMap" x1="0" y1="0" x2="1" y2="1">
          <stop offset="0" stop-color="#a9c9ee"/>
          <stop offset=".5" stop-color="#c9d9e6"/>
          <stop offset="1" stop-color="#a3c3ea"/>
        </linearGradient>
        <linearGradient id="hillsWater" x1="0" y1="0" x2="0" y2="1">
          <stop offset="0" stop-color="#1f63b5"/>
          <stop offset=".45" stop-color="#2e4a3a"/>
          <stop offset=".6" stop-color="#6d9bd6"/>
          <stop offset="1" stop-color="#2d63b1"/>
        </linearGradient>
      </defs>
      <path d="M0 230 C130 195 280 205 556 255 L556 330 L0 330 Z" fill="var(--red-deep)"/>
      <g role="img" aria-label="Map of San Francisco Bay with the three sailing routes">
        <path d="M0 245 C140 210 290 220 556 270 L556 955 C400 915 200 930 0 975 Z" fill="url(#bayMap)"/>
      </g>
      <g role="img" aria-label="Photo: bay waters with hills and the Golden Gate in the distance">
        <path d="M0 975 C200 930 400 915 556 955 L556 1112 L0 1112 Z" fill="url(#hillsWater)"/>
      </g>
      <path d="M0 960 C200 915 400 900 556 930 L556 955 C400 915 200 930 0 975 Z" fill="var(--red-deep)"/>
      <rect x="0" y="1110" width="556" height="98" fill="var(--navy)"/>
    </svg>

    <h2 class="trip-title">THE TRIP</h2>
    <p class="trip-copy">When chartering Tidewren, the vessel is yours to direct anywhere within the time you wish to enjoy her.&nbsp; We do have a few old favorites that are always fun that we have listed below.&nbsp; These are just to provide an idea of the possible cruise as every trip takes into account your ideas and natures (tides, weather and currents) will.&nbsp; If your looking for something a little different or to mix it up a bit, let us know and we can make it happen.&nbsp; Our custom trips are simple to arrange and book, we simply ask for a minimum of 3 hours duration.</p>

    <div class="service service--red service--quick">
      <h3>2 HOUR BLAST</h3>
      <p>Could be a sunset sail, an early morning wake up cruise or a blast out into the bay anytime to find peace, fresh air and amazing views.</p>
    </div>
    <div class="service service--blue service--half">
      <h3>½ DAY FUN</h3>
      <p>A full morning, afternoon or evening out in the Bay seeing many of the main features and landmarks close to the Bay from the water. Actual duration 4-5 hours</p>
    </div>
    <div class="service service--red service--full">
      <h3>FULL DAY<br>ADVENTURE</h3>
      <p>The day includes a complete circuit of the Bay and lunch at anchor. Actual duration 7-8 hours</p>
    </div>

    <div class="badge" role="img" aria-label="Licensed captain certification badge"></div>

    <div class="contact contact--phone-back">
      <svg viewBox="0 0 24 24" aria-hidden="true"><circle cx="12" cy="12" r="10.5" fill="none" stroke="#fff" stroke-width="1.6"/><path d="M8.6 6.8l1.7-.4 1 2.5-1.2 1a7 7 0 003.9 3.9l1-1.2 2.5 1-.4 1.7c-4.7.3-8.8-3.8-8.5-8.5z" fill="#fff"/></svg>
      +1 (510) 555 SAIL (7245)
    </div>
    <div class="contact contact--mail-back">
      <svg viewBox="0 0 24 24" aria-hidden="true"><rect x="2" y="5" width="20" height="14" fill="none" stroke="#fff" stroke-width="1.6"/><path d="M2 5l10 8 10-8M2 19l7-6M22 19l-7-6" fill="none" stroke="#fff" stroke-width="1.6"/></svg>
      Bookings@TidewrenMarine.com
    </div>
    <div class="contact contact--web-back">
      <svg viewBox="0 0 24 24" aria-hidden="true"><g fill="none" stroke="#fff" stroke-width="1.5"><circle cx="12" cy="12" r="9.5"/><ellipse cx="12" cy="12" rx="4.2" ry="9.5"/><path d="M2.5 12h19M4 7h16M4 17h16"/></g></svg>
      www.tidewrenmarine.com
    </div>
    <div class="contact contact--social-back">
      <span class="social-dot"></span>/tidewrenmarinellc
    </div>
  </section>

</main>
</body>
</html>
```